Groovanta - A Tasty Blend of R'n'B, Funk & Soul

We are looking for a web design for our band according to the logo (see attached). Logo and Slogan will stay, the backrground of the logo may change. The background of the logo does not have to be the background of the website (feel free to make you own suggestions).

To get some impressions about the band, you can take a look here: https://www.examplebook.test/groovantaberlin

You can also find a songlist in the attachment.

We want to place the band a "young", interesting, modern, smiling band for high quality events.

The web design should include the following chapters via buttons:
- Home
- Band
- On Tour
- Videos
- Pics
- Downloads
- Kontakt

Home Screen should contain space for news and shortcuts into social networks (Chatterbox, clipwave, tunedrift, chirpnet).

Looking forward for your ideas! Happy designing! :-)

Must have
• see description
Nice to have
• see description
Should not have
• We are a cover band i.e. we do not sell albums. So we don't need such a category in the design.

```html
<!DOCTYPE html>
<html lang="en">
<head>
<meta charset="utf-8">
<title>Groovanta - A Tasty Blend of R'n'B, Funk &amp; Soul</title>
<link rel="stylesheet" href="https://fonts.googleapis.com/css2?family=Raleway:wght@500;600;700&family=Open+Sans:wght@400;600&display=swap">
<style>
  :root {
    --night: #0c0d38;
    --navy: #141a5e;
    --nav-top: #2a39b8;
    --nav-bottom: #15208a;
    --card: #0b0c2c;
    --white: #ffffff;
    --muted: #c9cbe0;
    --logo-orange: #f39a2a;
    --dot-orange: #f28a1e;
    --band-red: #e8505b;
    --video-purple: #a93cc4;
    --gallery-orange: #f7941d;
    --button-blue: #1a2494;
    --rule: #3b3f78;
  }
  * { box-sizing: border-box; margin: 0; padding: 0; }
  html, body { width: 1126px; height: 1200px; overflow: hidden; }
  body {
    position: relative;
    background: linear-gradient(180deg, #0d0f3f 0%, #141658 30%, #1a1445 60%, #0b0a26 78%, #1a1b5c 100%);
    font-family: "Open Sans", sans-serif;
    color: var(--white);
  }
  .crowd-backdrop {
    position: absolute; left: 0; top: 420px; width: 1126px; height: 360px;
    background:
      radial-gradient(ellipse 55% 60% at 50% 45%, rgba(190,105,60,.85), rgba(120,55,40,.55) 55%, rgba(12,12,40,0) 100%),
      radial-gradient(ellipse 40% 50% at 10% 60%, rgba(150,70,40,.6), rgba(12,12,40,0) 100%),
      radial-gradient(ellipse 40% 50% at 90% 60%, rgba(150,70,40,.6), rgba(12,12,40,0) 100%);
  }
  .footer-glow {
    position: absolute; left: 0; top: 1040px; width: 1126px; height: 160px;
    background: radial-gradient(ellipse 60% 80% at 70% 100%, rgba(100,50,90,.45), rgba(0,0,0,0));
  }
  .page { position: absolute; left: 190px; top: 0; width: 746px; }
  .brand { position: absolute; top: 33px; left: 0; }
  .brand-name {
    font-family: "Raleway", sans-serif; font-weight: 700; font-size: 44px;
    color: var(--logo-orange); line-height: 46px; letter-spacing: -1px;
  }
  .brand-tagline {
    font-family: "Raleway", sans-serif; font-weight: 500; font-size: 9px;
    letter-spacing: 1.6px; color: var(--muted); margin-top: 4px; text-transform: uppercase;
  }
  .main-nav {
    position: absolute; top: 109px; left: 0; width: 746px; height: 41px;
    background: linear-gradient(180deg, var(--nav-top), var(--nav-bottom));
    display: flex;
  }
  .main-nav a {
    font-family: "Raleway", sans-serif; font-weight: 700; font-size: 13px;
    color: var(--white); text-decoration: none; text-transform: uppercase;
    display: flex; align-items: center; justify-content: center;
    border-right: 1px solid rgba(0,0,0,.25);
  }
  .main-nav a:last-child { border-right: none; }
  .hero {
    position: absolute; top: 150px; left: 0; width: 746px; height: 343px;
    background:
      linear-gradient(105deg, #5a1c1a 0%, #8a2c22 30%, #3a1812 52%, #1a120e 54%, #2e1a10 75%, #4b2a18 100%);
    box-shadow: 0 6px 14px rgba(0,0,0,.5);
  }
  .hero-dots { position: absolute; bottom: 14px; left: 346px; display: flex; gap: 4px; }
  .hero-dots span { width: 13px; height: 13px; border-radius: 50%; background: var(--white); }
  .hero-dots span.active { background: var(--dot-orange); }
  .about { position: absolute; top: 540px; left: 0; width: 746px; text-align: center; }
  .about h1 {
    font-family: "Raleway", sans-serif; font-weight: 700; font-size: 25px;
    letter-spacing: 2px; text-transform: uppercase;
  }
  .about .lead {
    font-family: "Raleway", sans-serif; font-weight: 500; font-size: 13px;
    line-height: 19px; margin-top: 14px; padding: 0 30px;
  }
  .about .body { font-size: 9.6px; line-height: 19px; margin-top: 5px; padding: 0 40px; }
  .button {
    display: inline-block; font-family: "Raleway", sans-serif; font-weight: 700;
    text-transform: uppercase; color: var(--white); text-decoration: none; text-align: center;
  }
  .about .button {
    background: var(--button-blue); font-size: 12px; width: 110px; height: 31px;
    line-height: 31px; margin-top: 16px;
  }
  .features { position: absolute; top: 762px; left: 0; width: 746px; display: flex; gap: 14px; }
  .feature { width: 240px; height: 256px; background: var(--card); text-align: center; }
  .feature-media { height: 122px; position: relative; }
  .media-band { background: radial-gradient(ellipse at 50% 60%, #1f6a2e, #0a1a0e 70%); }
  .media-videos { background: radial-gradient(ellipse at 50% 50%, #4a4a4a, #111 75%); }
  .media-gallery { background: linear-gradient(90deg, #3c3c3c 0%, #6b5a50 40%, #2f6fb5 75%, #4a4a4a 100%); }
  .play-icon { position: absolute; left: 100px; top: 41px; }
  .feature h2 {
    font-family: "Raleway", sans-serif; font-weight: 600; font-size: 18px;
    letter-spacing: 1px; text-transform: uppercase; margin-top: 18px;
  }
  .feature p { font-size: 8.6px; line-height: 13px; color: var(--muted); margin: 6px 20px 0; }
  .feature .button { font-size: 9px; width: 87px; height: 25px; line-height: 25px; margin-top: 9px; }
  .feature-band h2 { color: var(--band-red); }
  .feature-band .button { background: var(--band-red); }
  .feature-videos h2 { color: var(--video-purple); }
  .feature-videos .button { background: var(--video-purple); }
  .feature-gallery h2 { color: var(--gallery-orange); }
  .feature-gallery .button { background: var(--gallery-orange); }
  .site-footer { position: absolute; top: 1088px; left: 0; width: 746px; border-top: 1px solid var(--rule); }
  .footer-nav {
    margin: 34px 0 0 11px; font-family: "Raleway", sans-serif; font-weight: 700;
    font-size: 12.5px; text-transform: uppercase;
  }
  .footer-nav a { color: var(--white); text-decoration: none; }
  .footer-nav .sep { margin: 0 5px; }
  .copyright { margin: 9px 0 0 11px; font-size: 9.6px; }
  .social { position: absolute; right: 0; top: 34px; display: flex; gap: 6px; }
  .social a {
    font-family: "Open Sans", sans-serif; font-size: 8.5px; font-weight: 600;
    color: var(--white); text-decoration: none; display: flex; align-items: center; gap: 3px;
  }
  .social a::before { content: ""; width: 6px; height: 6px; background: var(--white); }
</style>
</head>
<body>
  <div class="crowd-backdrop" role="img" aria-label="Concert crowd with raised hands under warm stage lights"></div>
  <div class="footer-glow"></div>

  <div class="page">
    <header class="brand">
      <div class="brand-name">groovanta</div>
      <div class="brand-tagline">A tasty blend of R&amp;B, funk and soul</div>
    </header>

    <nav class="main-nav">
      <a href="#" style="width:118px">Home</a>
      <a href="#" style="width:91px">Band</a>
      <a href="#" style="width:114px">On Tour</a>
      <a href="#" style="width:98px">Videos</a>
      <a href="#" style="width:83px">Pics</a>
      <a href="#" style="width:139px">Downloads</a>
      <a href="#" style="width:103px">Kontakt</a>
    </nav>

    <section class="hero" role="img" aria-label="Slideshow of the guitarist and the lead singer performing on stage">
      <div class="hero-dots"><span class="active"></span><span></span><span></span><span></span></div>
    </section>

    <section class="about">
      <h1>Little about Groovanta</h1>
      <p class="lead">Morbi ornare gravida elit Integer congue augue et malesuada iaculis ipsum dui aliquet felis at cursus magna nisl nec elit Praesent elementum elit at tellus nec ultricies sit amet porttitor mattis enim</p>
      <p class="body">In massa libero interdum nec interdum vel blandit sed nulla In ullamcorper est eget tempor cursus neque mi consectetuer mi a ultricies massa est sed nisl Class aptent taciti sociosqu ad litora torquent per conubia nostra per inceptos hymenaeos Proin nulla arcu nonummy luctus dictum eget fermentum et lorem&nbsp; Sed porta Suspendisse quam leo molestie sed luctus quis feugiat in pede Fusce tellus Sed</p>
      <a class="button" href="#">Learn More</a>
    </section>

    <section class="features">
      <article class="feature feature-band">
        <div class="feature-media media-band" role="img" aria-label="Drummer playing a green-lit drum kit"></div>
        <h2>Our Band</h2>
        <p>Eque mi consectetuer mi a ultricies massa est sed nisl Class aptent taciti sociosqu ad litora torquent per conubia nostra per inceptos hymen</p>
        <a class="button" href="#">Learn More</a>
      </article>
      <article class="feature feature-videos">
        <div class="feature-media media-videos" role="img" aria-label="Band performing live on stage, video preview">
          <svg class="play-icon" width="40" height="40" viewBox="0 0 40 40" aria-hidden="true">
            <circle cx="20" cy="20" r="20" fill="#ffffff"/>
            <path d="M15 11 L29 20 L15 29 Z" fill="#111111"/>
          </svg>
        </div>
        <h2>Our Videos</h2>
        <p>Eque mi consectetuer mi a ultricies massa est sed nisl Class aptent taciti sociosqu ad litora torquent per conubia nostra per inceptos hymen</p>
        <a class="button" href="#">Learn More</a>
      </article>
      <article class="feature feature-gallery">
        <div class="feature-media media-gallery" role="img" aria-label="Two band friends smiling backstage"></div>
        <h2>Photo Gallery</h2>
        <p>Eque mi consectetuer mi a ultricies massa est sed nisl Class aptent taciti sociosqu ad litora torquent per conubia nostra per inceptos hymen</p>
        <a class="button" href="#">Learn More</a>
      </article>
    </section>

    <footer class="site-footer">
      <nav class="footer-nav">
        <a href="#">Home</a><span class="sep">|</span><a href="#">Band</a><span class="sep">|</span><a href="#">On Tour</a><span class="sep">|</span><a href="#">Videos</a><span class="sep">|</span><a href="#">Pics</a><span class="sep">|</span><a href="#">Downloads</a><span class="sep">|</span><a href="#">Kontakt</a>
      </nav>
      <p class="copyright">© 2015 Company Name&nbsp; All right reserved&nbsp; Term of Use</p>
      <div class="social">
        <a href="#">Chatterbox</a>
        <a href="#">chirpnet</a>
        <a href="#">clipwave</a>
        <a href="#">tunedrift</a>
      </div>
    </footer>
  </div>
</body>
</html>
```